wealth management firm, professional group, new model

we have a logo that works but we need a card, white background using our colors...clean look

our tag line if can be used in

The Bridge From Client to Owner

```html
<!DOCTYPE html>
<html lang="en">
<head>
<meta charset="UTF-8">
<title>Arcova Wealth Partners – Business Card</title>
<link rel="stylesheet" href="https://fonts.googleapis.com/css2?family=Montserrat:ital,wght@0,400;0,500;1,400&display=swap">
<style>
  :root {
    --stage: #232323;
    --paper: #eeeeee;
    --navy: #14284a;
    --on-navy: #e4e8ef;
    --rule: #6c7a93;
  }
  * { box-sizing: border-box; margin: 0; padding: 0; }
  html, body { width: 1200px; height: 576px; overflow: hidden; }
  body {
    background: var(--stage);
    font-family: "Montserrat", sans-serif;
    position: relative;
  }
  .card {
    position: absolute;
    width: 484px;
    height: 292px;
    border-radius: 9px;
    background: var(--paper);
    overflow: hidden;
  }
  .card--front { left: 102px; top: 139px; }
  .card--back { left: 596px; top: 138px; }

  /* Front */
  .front-wordmark {
    position: absolute;
    left: 0; right: 0;
    text-align: center;
    color: var(--navy);
    font-weight: 400;
  }
  .front-wordmark__name {
    top: 130px;
    font-size: 35px;
    letter-spacing: 0.38em;
    padding-left: 0.38em;
  }
  .front-wordmark__line {
    top: 190px;
    font-size: 14px;
    letter-spacing: 0.16em;
    padding-left: 0.16em;
  }

  /* Back */
  .back-top {
    position: absolute;
    left: 0; top: 0;
    width: 100%;
    height: 157px;
    text-align: center;
  }
  .back-top__name {
    position: absolute;
    left: 0; right: 0; top: 98px;
    color: var(--navy);
    font-size: 21px;
    font-weight: 400;
    letter-spacing: 0.11em;
  }
  .back-top__tagline {
    position: absolute;
    left: 0; right: 0; top: 128px;
    color: var(--navy);
    font-size: 10.5px;
    font-style: italic;
    letter-spacing: 0.04em;
  }
  .back-band {
    position: absolute;
    left: 0; bottom: 0;
    width: 100%;
    height: 135px;
    background: var(--navy);
    color: var(--on-navy);
  }
  .person {
    position: absolute;
    left: 63px; top: 42px;
  }
  .person__name { font-size: 21px; font-weight: 400; line-height: 1.1; }
  .person__title { font-size: 12.5px; margin-top: 2px; }
  .divider {
    position: absolute;
    left: 218px; top: 38px;
    width: 1px; height: 56px;
    background: var(--rule);
  }
  .contact {
    position: absolute;
    left: 252px; top: 36px;
    list-style: none;
    font-size: 12.5px;
  }
  .contact li {
    display: flex;
    align-items: center;
    height: 20px;
  }
  .contact svg {
    width: 10px; height: 10px;
    margin-right: 9px;
    fill: var(--on-navy);
    flex: none;
  }
</style>
</head>
<body>

<section class="card card--front" aria-label="Card front">
  <div class="front-wordmark front-wordmark__name">ARCOVA</div>
  <div class="front-wordmark front-wordmark__line">WEALTH PARTNERS</div>
</section>

<section class="card card--back" aria-label="Card back">
  <div class="back-top">
    <div class="back-top__name">ARCOVA WEALTH PARTNERS</div>
    <div class="back-top__tagline">The Bridge from Client to Owner</div>
  </div>
  <div class="back-band">
    <div class="person">
      <div class="person__name">Daniel Reyes</div>
      <div class="person__title">Managing Director</div>
    </div>
    <div class="divider"></div>
    <ul class="contact">
      <li>
        <svg viewBox="0 0 10 10" aria-hidden="true"><path d="M1 3.2C1 2 2.4 1.4 5 1.4S9 2 9 3.2V4H7V3.2H3V4H1Z M2.5 4.6h5l1 3.6v.8h-7v-.8Z"/></svg>
        555-014-2290
      </li>
      <li>
        <svg viewBox="0 0 10 10" aria-hidden="true"><path d="M0.5 2h9v6h-9Z M1.2 2.6 5 5.6 8.8 2.6v-.1H1.2Z" fill-rule="evenodd"/></svg>
        daniel@arcovawealth.com
      </li>
      <li>
        <svg viewBox="0 0 10 10" aria-hidden="true"><path d="M5 .8a4.2 4.2 0 1 0 0 8.4A4.2 4.2 0 0 0 5 .8Zm0 .9c.6.6 1 1.6 1.1 2.8H3.9C4 3.3 4.4 2.3 5 1.7Zm-1.1 3.6h2.2C6 6.5 5.6 7.5 5 8.1c-.6-.6-1-1.6-1.1-2.8ZM1.7 4.5a3.3 3.3 0 0 1 1.8-2.5c-.3.7-.5 1.5-.5 2.5Zm0 .8H3c0 1 .2 1.8.5 2.5a3.3 3.3 0 0 1-1.8-2.5Zm6.6 0a3.3 3.3 0 0 1-1.8 2.5c.3-.7.5-1.5.5-2.5Zm0-.8H7c0-1-.2-1.8-.5-2.5a3.3 3.3 0 0 1 1.8 2.5Z"/></svg>
        www.arcovawealth.com
      </li>
    </ul>
  </div>
</section>

</body>
</html>
```